New Business Card for Odd Fern Designs

I create and make jewellery and Clothing. But when it comes to business card design I fail completely.

Sketching is my area, drawing, putting things together neatly, not so much.

Here is a little blurb about my company:

Odd Fern Designs is a truly unique customer experience. Work one on one with Owner Petra Wolcott to make your costuming dreams come true.

Not after a costume? Browse through the store for a look at beautiful and unique piece of jewellery. Each piece has been put together by Petra, by hand. You'll find Steampunk, gothic, lolita and other quirky styles.

Want something else? What abotu a pair of warm kitty paws? A Pair of Kitty ears? A pony tail to wear on your jeans? There are so many options and things to choose! You will want to take it all home.

I have attached the previous business card with my mascot "Greta" As you can see there is a very Greta in Cloudmere feel to the overall company, with references to The Tin Tinker, and the idea that "We are all made here".

Colour's to use would be purple and blue. The winning design would show the unique but professional approach that Odd Fern Designs takes when creating each piece for their customers.

Reason: Wanted to give you a chance to go over feed back that has been sent out. I am committed to paying for the design that I will use. I think another week will help tweak things up.

Target Market(s)

Nerds, Geeks and Sci-Fi people aged 20 - 34 both Male and Female

Industry/Entity Type

Store

Requirements
Must have
• Website address: www.oddferndesigns.example

Yeah, rest is up too you!
Nice to have
• Honestly, if you could make the whole thing look like a Edwin Marlowe "Greta in Cloudmere" Drawing with the same line working style that would be amazing!

But I won't restrict you! I'd like to see what you can come up with.

```html
<!DOCTYPE html>
<html lang="en">
<head>
<meta charset="utf-8">
<title>Odd Fern Designs – Business Card</title>
<link rel="stylesheet" href="https://fonts.googleapis.com/css2?family=Oleo+Script:wght@400;700&display=swap">
<style>
  :root {
    --page: #ffffff;
    --teal: #00adbe;
    --mist: #dde0e6;
    --plum: #8c3c92;
    --plum-back: #8a3c93;
    --name-brown: #6b4f1c;
    --rule-tan: #b5955a;
    --email-gold: #a7813a;
    --web-orange: #f4961c;
    --tagline-gold: #f0b64a;
    --figure-top: #7a4a4a;
    --figure-mid: #c9a6b0;
    --figure-low: #b98aa6;
  }
  * { margin: 0; padding: 0; box-sizing: border-box; }
  html, body { width: 1200px; height: 1032px; overflow: hidden; background: var(--page); }
  .canvas { position: relative; width: 1200px; height: 1032px; }

  .card { position: absolute; width: 465px; height: 803px; }

  .card-front {
    left: 113px; top: 113px;
    background: linear-gradient(to bottom,
      var(--teal) 0%, var(--teal) 14%,
      #7cc6d0 38%, var(--mist) 62%,
      #d6ccd8 74%, #b48cb4 88%, var(--plum) 100%);
    overflow: hidden;
  }
  .card-front::before, .card-front::after {
    content: ""; position: absolute; top: 0; bottom: 0; width: 62px;
    background: rgba(0, 60, 80, 0.06);
  }
  .card-front::before { left: 0; }
  .card-front::after { right: 0; }

  .card-back { left: 622px; top: 116px; background: var(--plum-back); }

  .contact {
    position: absolute; left: 78px; width: 310px; top: 203px;
    font-family: "Oleo Script", cursive;
  }
  .owner-name {
    font-size: 37px; font-weight: 700; color: var(--name-brown);
    line-height: 44px; white-space: nowrap;
  }
  .name-rule { height: 1px; background: var(--rule-tan); margin: 5px 0 8px; }
  .email { font-size: 19px; font-weight: 700; color: var(--email-gold); line-height: 30px; white-space: nowrap; }
  .website { font-size: 19px; font-weight: 700; color: var(--web-orange); line-height: 30px; white-space: nowrap; }
  .tagline {
    font-size: 44px; font-weight: 700; color: var(--tagline-gold);
    line-height: 44px; margin-top: 2px; white-space: nowrap;
  }

  .mascot {
    position: absolute; left: 70px; top: 475px; width: 315px; height: 268px;
  }
</style>
</head>
<body>
<div class="canvas">
  <section class="card card-front">
    <div class="contact">
      <div class="owner-name">Petra Wolcott</div>
      <div class="name-rule"></div>
      <div class="email">petra@oddfernmail.example</div>
      <div class="website">www.oddferndesigns.example</div>
      <div class="tagline">Handcrafted<br>flighs of fancy</div>
    </div>
    <svg class="mascot" viewBox="0 0 315 268" role="img" aria-label="Illustration of the mascot Greta in a tall top hat, sitting on the ground">
      <defs>
        <linearGradient id="mascot-tone" x1="0" y1="0" x2="0" y2="1">
          <stop offset="0" stop-color="var(--figure-top)"/>
          <stop offset="0.3" stop-color="var(--figure-mid)"/>
          <stop offset="1" stop-color="var(--figure-low)"/>
        </linearGradient>
      </defs>
      <rect x="0" y="0" width="315" height="268" rx="30" fill="url(#mascot-tone)" opacity="0.55"/>
    </svg>
  </section>
  <section class="card card-back"></section>
</div>
</body>
</html>
```